Business card design for new eCommerce site focusing on integrity and strong businsess tactics

We need a business card that will stand out and be memorable. Something with color that matches our company logo colors. Think high end version of Pactivo. There are 2 logos provided. The parent company is called Amber Ledge Partners and we are presenting a new and very exciting eCommerce site called BrightHarborTrade.example.

Target Market(s)

Our target markets are in the Activities, Food and Beverage, Health and Beauty

Industry/Entity Type

Marketing

Contact Information for Business Card

We have 4 members that need cards...I will provide all info to the winner of the design contest
Business Address is
4870 West 63rd Avenue, Suite C207
Phoenix AZ 85731

Font styles to use
Serif
Sans Serif

Colors

Designer to choose colors to be used in the design.

Requirements
Must have
• The card must be memorable...should be unique in design but must exude integrity and be playful .
• I have provided several colors or our parent company...please feel free to use which ever
Nice to have
• I will leave this up to you. Feel free to use other images of your choosing that wraps around our client.....Activities, Dining, Health, Beauty
Should not have
• just dont be boring

```html
<!DOCTYPE html>
<html lang="en">
<head>
<meta charset="utf-8">
<title>Amber Ledge Partners – Business Card</title>
<link href="https://fonts.googleapis.com/css2?family=Arimo:wght@400;700&display=swap" rel="stylesheet">
<style>
  :root {
    --backdrop: #253203;
    --card-green: #86ab2f;
    --brand-green: #a9cb4c;
    --paper: #ffffff;
  }
  html, body {
    margin: 0;
    padding: 0;
    width: 1200px;
    height: 1200px;
    overflow: hidden;
    background: var(--backdrop);
  }
  .canvas {
    position: relative;
    width: 1200px;
    height: 1200px;
    font-family: "Arimo", Arial, sans-serif;
  }
  .card {
    position: absolute;
    left: 242px;
    width: 731px;
    height: 438px;
    background: var(--paper);
  }
  .card--front { top: 101px; }
  .card--back { top: 622px; }
  .card svg { display: block; width: 100%; height: 100%; }
  .brand-name { font-weight: 700; fill: var(--brand-green); }
  .headline { font-weight: 700; fill: var(--paper); }
  .address { font-weight: 400; fill: var(--paper); }
</style>
</head>
<body>
<main class="canvas">
  <section class="card card--front" aria-label="Card front">
    <svg viewBox="0 0 914 548" xmlns="http://www.w3.org/2000/svg">
      <rect class="green-field" width="914" height="548" fill="var(--card-green)"/>
      <path class="cloud-panel" fill="var(--paper)"
        d="M0 0 H150 C143 35 152 70 186 112 C265 96 345 145 370 240 C420 252 452 292 452 325 C500 385 495 470 435 548 H0 Z"/>
      <circle class="brand-dot" cx="241" cy="277" r="105" fill="var(--brand-green)"/>
      <text class="brand-name" x="241" y="432" font-size="40" text-anchor="middle">Amber Ledge</text>
      <text class="brand-name" x="241" y="476" font-size="40" text-anchor="middle">Partners</text>

      <text class="headline" x="872" y="150" font-size="50" text-anchor="end">Amber Ledge Partners</text>

      <g class="home-icon" fill="var(--paper)" transform="translate(668 385)">
        <path d="M-15 0 L0 -13 L15 0 L12 3 L0 -8 L-12 3 Z"/>
        <path d="M-9 1 L0 -7 L9 1 V12 H3 V5 H-3 V12 H-9 Z"/>
      </g>
      <text class="address" x="668" y="423" font-size="17" text-anchor="middle">4870 West 63rd Avenue,</text>
      <text class="address" x="668" y="451" font-size="17" text-anchor="middle">Suite C207 Phoenix AZ 85731</text>
    </svg>
  </section>

  <section class="card card--back" aria-label="Card back">
    <svg viewBox="0 0 914 548" xmlns="http://www.w3.org/2000/svg">
      <circle class="brand-dot" cx="469" cy="234" r="105" fill="var(--brand-green)"/>
      <text class="brand-name" x="469" y="390" font-size="40" text-anchor="middle">Amber Ledge</text>
      <text class="brand-name" x="469" y="434" font-size="40" text-anchor="middle">Partners</text>
    </svg>
  </section>
</main>
</body>
</html>
```